Updated website design needed for Radiology Group, Pine Hollow Imaging Partners

Clean, uncluttered, updated design needed for top regional Radiology Center. Focus on personal, patient oriented design, (not clinical). Should be simple and easy to navigate, with clear CTAs. Use blues, greens and photos of people in the Central Oregon outdoors.
Uncoded, PSD design only. 2 pages: Home page and one example interior page.
reference current site: http://www.phipclinic-example.com/
Sites they like:
http://www.valescanlabs-example.com/
http://www.tbmx-example.net/handler.cfm?event=practice,main
http://www.kestrelbonecare-example.com/

Medical Imaging

2 page

Sans Serif

• Personal and patient friendly.
• Lots of white space, clean and uncluttered. Clear CTAs, such as: Patient Bill Pay, Make an Appointment, Meet Our Doctors
• Use copy and contact information from the current site.
• Use outdoor images from Central Oregon, late Winter/ Spring (snow, light colors, spring green, for example)
• Include one example interior page, either Your Exam or Meet Our Doctors
• The client likes:
• Meet Our Doctors slider section, and big, easy to navigate Information Center on www.kestrelbonecare-example.com
• The personal feel of the Your Exam section on www.valescanlabs-example.com
• Blues and Greens, outdoorsy imagery
• The client does not like:
• complex drop down menus
• clinical feel
• Do not use lorum ipsum or dummy text.
• Do not use outdoor images from other regions. Do not use Summer (hot, poolside) or Fall (red/orange leaves) images.

```html
<!DOCTYPE html>
<html lang="en">
<head>
<meta charset="utf-8">
<title>Pine Hollow Imaging Partners</title>
<link rel="stylesheet" href="https://fonts.googleapis.com/css2?family=Titillium+Web:wght@400;600;700;900&family=Open+Sans:wght@400;600;700&display=swap">
<style>
:root{
  --blue:#00b9f2;
  --blue-dark:#0aa3d6;
  --green:#8cbd0a;
  --ink:#333;
  --text:#444;
  --muted:#777;
  --pale:#e9edf4;
  --grey:#eeeeee;
  --footer:#333333;
  --footer-deep:#262626;
  --white:#fff;
}
*{box-sizing:border-box;margin:0;padding:0}
html,body{width:1200px;height:2616px;overflow:hidden}
body{position:relative;background:var(--white);font-family:"Open Sans",sans-serif;color:var(--text)}
.abs{position:absolute}
h2.section-title{position:absolute;left:0;width:1200px;text-align:center;font-family:"Titillium Web",sans-serif;font-weight:400;font-size:30px;color:var(--ink)}
.divider{position:absolute;left:385px;width:430px;height:20px}
.btn{position:absolute;display:flex;align-items:center;justify-content:center;font-family:"Open Sans",sans-serif;font-weight:700;font-size:13px;background:var(--blue);color:var(--white);border-radius:2px}

/* header */
.site-header{top:0;left:0;width:1200px;height:97px;background:#f7f7f7}
.brand{left:160px;top:22px;display:flex;align-items:center;gap:12px}
.brand-mark{width:50px;height:50px;background:#6b6fa8}
.brand-name{font-family:"Titillium Web",sans-serif;font-weight:600;font-size:20px;line-height:22px;color:#3d3d5c;width:190px}
.topbar{top:0;left:700px;height:30px;display:flex}
.topbar .phone{background:var(--blue);color:var(--white);font-weight:700;font-size:15px;display:flex;align-items:center;gap:8px;padding:0 16px 0 24px;border-radius:0 0 0 16px}
.topbar .book{background:var(--green);color:var(--white);font-weight:700;font-size:14px;display:flex;align-items:center;padding:0 26px 0 16px;clip-path:polygon(0 0,100% 0,91% 100%,0 100%)}
.main-nav{top:97px;left:0;width:1200px;height:41px;background:var(--blue);display:flex;padding-left:143px}
.main-nav a{font-size:12px;color:var(--white);text-decoration:none;display:flex;align-items:center;padding:0 20px}
.main-nav a.active{background:var(--green);font-weight:700;padding:0 17px}

/* hero */
.hero{top:138px;left:0;width:1200px;height:408px;background:linear-gradient(180deg,#b9cfe3 0%,#dfe7ee 45%,#f2f5f7 75%,#e4e9ee 100%)}
.hero-caption{top:320px;left:0;width:1200px;height:88px;background:rgba(40,40,40,.82);color:var(--white);font-family:"Titillium Web",sans-serif;font-size:27px;line-height:36px;text-align:center;padding-top:8px}

/* welcome */
.welcome-text{top:680px;left:160px;width:880px;text-align:center;font-size:12.5px;line-height:24px;color:var(--text)}

/* services */
.services{top:876px;left:0;width:1200px;height:552px;background:var(--pale)}
.service-card{position:absolute;width:285px;height:186px;background:var(--white);padding:6px 6px 0}
.service-card .photo{height:118px}
.service-card .label{position:absolute;left:0;bottom:0;width:285px;height:56px;background:var(--blue);color:var(--white);font-family:"Titillium Web",sans-serif;font-size:20px;display:flex;align-items:center;justify-content:center}
.service-card.featured .label{background:var(--green)}

/* audiences */
.audience{top:1428px;height:337px;color:var(--white);text-align:center}
.audience h3{font-family:"Titillium Web",sans-serif;font-weight:900;font-size:32px;margin-top:8px}
.audience p{font-size:15px;line-height:26px;width:420px;margin:10px auto 0;font-weight:600}
.audience .read{display:inline-flex;margin-top:20px;width:100px;height:34px;background:var(--white);color:var(--ink);font-size:13px;font-weight:600;align-items:center;justify-content:center;border-radius:2px}
.audience svg{margin-top:38px}

/* bill pay & physicians */
.block-title{font-family:"Titillium Web",sans-serif;font-size:27px;color:var(--ink)}
.rule{height:1px;background:#ddd}
.bill-links{list-style:none;font-size:11.5px;line-height:19px}
.bill-links li{position:relative;padding-left:14px;margin-bottom:17px;color:var(--ink);font-weight:600;text-decoration:underline}
.bill-links li::before{content:"›";position:absolute;left:0;color:var(--blue);text-decoration:none}
.doc{position:absolute;top:1866px;width:94px;height:120px}
.doc .photo{height:100px}
.doc .name{height:20px;background:var(--blue);color:var(--white);font-size:10.5px;font-weight:600;display:flex;align-items:center;justify-content:center}

/* reviews */
.reviews{top:2045px;left:0;width:1200px;height:330px;background:var(--grey)}
.avatar{left:170px;top:2135px;width:110px;height:110px;border-radius:50%;border:4px solid #333;background:linear-gradient(160deg,#c9b8a8,#8a7a6c)}
.quote{left:318px;top:2140px;width:722px;font-size:11.5px;line-height:21px;color:var(--text)}
.reviewer{left:318px;top:2245px;font-family:"Titillium Web",sans-serif;font-weight:700;font-size:16px;color:var(--blue)}
.dots{left:997px;top:2276px;display:flex;gap:5px}
.dots span{width:8px;height:8px;border-radius:50%;background:#bbb}
.dots span.on{background:var(--white);border:2px solid #5cc3a4}

/* footer */
.footer-col h4{font-family:"Titillium Web",sans-serif;font-size:15px;color:var(--white);font-weight:700;margin-bottom:18px}
.footer-links{display:grid;grid-template-columns:108px 130px;row-gap:7px;list-style:none;font-size:11px;color:#ddd}
.footer-links li::before{content:"› ";color:#aaa}
.field{width:190px;height:20px;background:var(--white);border-radius:2px;margin-bottom:7px;font-size:10px;font-style:italic;color:#999;padding:3px 6px}
.field.message{height:34px}
.submit{display:inline-block;background:var(--green);color:var(--white);font-size:10px;padding:3px 10px;border-radius:2px}
.contact-row{display:flex;gap:12px;font-size:11px;color:#ddd;line-height:16px;margin-bottom:18px}
.copyright{top:2578px;left:0;width:1200px;height:38px;background:var(--footer-deep);color:#ccc;font-size:11px;padding:12px 0 0 162px}
.social{top:2586px;left:944px;display:flex;gap:8px}
.social span{width:24px;height:24px;border-radius:50%;background:var(--blue)}
.social span:first-child{background:var(--green)}
</style>
</head>
<body>

<header class="site-header abs">
  <div class="brand abs">
    <span class="brand-mark"></span>
    <span class="brand-name">Pine Hollow Imaging Partners</span>
  </div>
  <div class="topbar abs">
    <span class="phone">
      <svg width="16" height="16" viewBox="0 0 16 16"><circle cx="8" cy="8" r="7" fill="none" stroke="#fff" stroke-width="1.5"/><path d="M5.5 4.5l1.5 1.5-1 1c.6 1.3 1.6 2.3 2.9 2.9l1-1 1.6 1.5-1.2 1.2c-2.8-.6-5.3-3.1-5.9-5.9z" fill="#fff"/></svg>
      (541) 555-0148</span>
    <span class="book">Book An Appointment</span>
  </div>
</header>

<nav class="main-nav abs">
  <a class="active">Home</a><a>About Us</a><a>Our Services</a><a>For Patients</a><a>Our Physicians</a><a>For Physicians</a><a>PACS &amp; Documents</a><a>Appointments</a><a>Our Locations</a>
</nav>

<section class="hero abs" role="img" aria-label="Two cross-country skiers on a snowy trail between frosted pine trees under a pale winter sky">
  <div class="hero-caption abs">Provide Quality Diagnostic Imaging Services To The<br>Central And Eastern Oregon Communities</div>
</section>

<h2 class="section-title" style="top:590px">Welcome to Pine Hollow Imaging Partners</h2>
<svg class="divider" style="top:643px" viewBox="0 0 430 20"><line x1="0" y1="10" x2="200" y2="10" stroke="#ccc"/><line x1="230" y1="10" x2="430" y2="10" stroke="#ccc"/><circle cx="215" cy="10" r="7" fill="#8aa3c8"/></svg>
<p class="welcome-text abs">Pine Hollow Imaging Partners is a diagnostic imaging corporation providing professional services to Central and Eastern Oregon hospitals and clinics as well as state-of-the-art services in its' own outpatient imaging center. PHIP was established by its' founder, Walter H. Prescott, MD when he opened his Central Oregon practice in 1947. PHIP is staffed by fellowship trained physicians with expertise in major disciplines to include mammography, ultrasound, Magnetic Resonance Imaging, Computed Tomography, Positron Emission Tomography,...</p>
<span class="btn" style="left:549px;top:790px;width:100px;height:34px">Read More</span>

<section class="services abs">
  <h2 class="section-title" style="top:32px">Our Services</h2>
  <svg class="divider" style="top:84px" viewBox="0 0 430 20"><line x1="0" y1="10" x2="200" y2="10" stroke="#ccc"/><line x1="230" y1="10" x2="430" y2="10" stroke="#ccc"/><circle cx="215" cy="10" r="7" fill="#8aa3c8"/></svg>
  <div class="service-card featured" style="left:160px;top:119px"><div class="photo" role="img" aria-label="MRI scanner in a bright room" style="background:linear-gradient(135deg,#eef0f2,#c9ced4)"></div><div class="label">MRI</div></div>
  <div class="service-card" style="left:459px;top:119px"><div class="photo" role="img" aria-label="CT scanner with patient table" style="background:linear-gradient(135deg,#f4f5f6,#d3d7db)"></div><div class="label">CT-64</div></div>
  <div class="service-card" style="left:755px;top:119px"><div class="photo" role="img" aria-label="X-ray image of two hands" style="background:radial-gradient(circle at 50% 50%,#9a9a9a,#1a1a1a 70%)"></div><div class="label">X-Ray</div></div>
  <div class="service-card" style="left:160px;top:327px"><div class="photo" role="img" aria-label="Nuclear medicine scanner" style="background:linear-gradient(135deg,#e8ecec,#b8c6c4)"></div><div class="label">Nuclear Medicine</div></div>
  <div class="service-card" style="left:459px;top:327px"><div class="photo" role="img" aria-label="PET scanner in a clinic room" style="background:linear-gradient(135deg,#eef3ea,#cdd6c8)"></div><div class="label">PET</div></div>
  <div class="service-card" style="left:755px;top:327px"><div class="photo" role="img" aria-label="Ultrasound scan image" style="background:radial-gradient(ellipse at 50% 60%,#777,#111 70%)"></div><div class="label">Ultrasound</div></div>
</section>

<section class="audience abs" style="left:0;width:599px;background:linear-gradient(135deg,#6b6b6b,#4a4a4a)" role="img" aria-label="Doctor with a patient, dimmed photo background">
  <svg width="76" height="66" viewBox="0 0 76 66"><rect x="22" y="4" width="50" height="36" fill="none" stroke="#fff" stroke-width="4"/><circle cx="12" cy="10" r="6" fill="#fff"/><rect x="6" y="18" width="12" height="26" fill="#fff"/><rect x="6" y="44" width="5" height="18" fill="#fff"/><rect x="13" y="44" width="5" height="18" fill="#fff"/><line x1="18" y1="22" x2="36" y2="14" stroke="#fff" stroke-width="3"/><line x1="47" y1="40" x2="40" y2="60" stroke="#fff" stroke-width="3"/><line x1="47" y1="40" x2="54" y2="60" stroke="#fff" stroke-width="3"/></svg>
  <h3>For Patients</h3>
  <p>This page is to help guide you through our web site. We are happy to help you in any way we can, if you have any questions please contact us directly @ 541.555.0148.</p>
  <span class="read">Read More</span>
</section>
<section class="audience abs" style="left:599px;width:601px;background:linear-gradient(135deg,#3fc6f2,#13b0ea)" role="img" aria-label="Group of medical staff, tinted blue photo background">
  <svg width="76" height="66" viewBox="0 0 76 66"><rect x="22" y="4" width="50" height="36" fill="none" stroke="#fff" stroke-width="4"/><circle cx="12" cy="10" r="6" fill="#fff"/><rect x="6" y="18" width="12" height="26" fill="#fff"/><rect x="6" y="44" width="5" height="18" fill="#fff"/><rect x="13" y="44" width="5" height="18" fill="#fff"/><line x1="18" y1="22" x2="36" y2="14" stroke="#fff" stroke-width="3"/><line x1="47" y1="40" x2="40" y2="60" stroke="#fff" stroke-width="3"/><line x1="47" y1="40" x2="54" y2="60" stroke="#fff" stroke-width="3"/></svg>
  <h3>For Physicians</h3>
  <p>Pine Hollow Imaging Partners is a diagnostic imaging corporation providing professional services to Central and Eastern Oregon hospitals and clinics</p>
  <span class="read">Read More</span>
</section>

<section class="bill-pay abs" style="left:160px;top:1808px;width:405px">
  <h3 class="block-title">Online Bill Pay</h3>
  <div class="rule" style="margin-top:6px"></div>
  <div role="img" aria-label="Hands holding a payment card over a laptop keyboard" style="position:absolute;top:50px;left:0;width:197px;height:132px;background:linear-gradient(135deg,#e3eaf0,#9fb3c4)"></div>
  <ul class="bill-links" style="position:absolute;top:55px;left:212px;width:180px">
    <li>BILLPAY Pine Hollow Imaging Partners</li>
    <li>BILLPAY Pine Hollow MRI</li>
    <li>BILLPAY Juniper Ridge Imaging</li>
  </ul>
</section>

<section class="physicians abs" style="left:628px;top:1808px;width:411px">
  <h3 class="block-title">Our Physicians</h3>
  <div class="rule" style="margin-top:6px"></div>
</section>
<div class="doc" style="left:628px"><div class="photo" role="img" aria-label="Portrait of Dr. Owen Marsh" style="background:linear-gradient(180deg,#9aa7b3,#2f3a4a)"></div><div class="name">Owen Marsh</div></div>
<div class="doc" style="left:733px"><div class="photo" role="img" aria-label="Portrait of Dr. Lena Hartwell" style="background:linear-gradient(180deg,#b3aca5,#3c3a3e)"></div><div class="name">Lena Hartwell</div></div>
<div class="doc" style="left:839px"><div class="photo" role="img" aria-label="Portrait of Dr. Curtis Vale" style="background:linear-gradient(180deg,#8fb4d8,#2d5e9a)"></div><div class="name">Curtis Vale</div></div>
<div class="doc" style="left:945px"><div class="photo" role="img" aria-label="Portrait of Dr. Gordon T. Reese" style="background:linear-gradient(180deg,#a9adb0,#3b3c40)"></div><div class="name">Gordon T. Reese</div></div>

<section class="reviews abs">
  <h2 class="section-title" style="top:24px;font-size:27px">Patient Reviews</h2>
  <svg class="divider" style="top:66px" viewBox="0 0 430 20"><line x1="0" y1="10" x2="200" y2="10" stroke="#ccc"/><line x1="230" y1="10" x2="430" y2="10" stroke="#ccc"/><circle cx="215" cy="10" r="7" fill="#8aa3c8"/></svg>
</section>
<div class="avatar abs" role="img" aria-label="Portrait of the reviewing patient"></div>
<svg class="abs" style="left:313px;top:2128px" width="30" height="22" viewBox="0 0 30 22"><path d="M2 20V11C2 5 6 2 12 1v4c-3 1-5 3-5 6h5v9zM17 20V11c0-6 4-9 10-10v4c-3 1-5 3-5 6h5v9z" fill="#d6d6d6"/></svg>
<p class="quote abs">&nbsp;&nbsp;&nbsp;&nbsp;&nbsp;&nbsp;Lorem ipsum dolor smit amet, consectetuer adipiscing elitmk, sed amet diam nonummy nibh euismod tincidun nt ut laoreetml dolore magna aliquam erat volutpat. Ut wisi enim ad minim veniam, quis nostrud exer tationk ullamcorpi per suscipit lobortisk nisl utml aliqpi ex ea commodo consequat. Duis autem vel eumk iriure dolor inj hendrerit inn vulputate velit esse molestiemo consequat, velhki illumn gnol dolore eu feugiat nulla facilisis .</p>
<div class="abs" style="left:318px;top:2236px;width:722px;height:1px;background:#ccc"></div>
<div class="reviewer abs">- Mr. Darren Oakley</div>
<div class="dots abs"><span class="on"></span><span></span><span></span></div>

<svg class="abs" style="left:0;top:2300px" width="1200" height="280" viewBox="0 0 1200 280" preserveAspectRatio="none">
  <path d="M0 120 Q600 -20 1200 120 V280 H0Z" fill="#333"/>
  <path d="M0 120 Q600 -20 1200 120" fill="none" stroke="#00b9f2" stroke-width="5"/>
  <path d="M0 100 Q600 -40 1200 100" fill="none" stroke="#00b9f2" stroke-width="2"/>
</svg>

<footer>
  <div class="footer-col abs" style="left:208px;top:2392px">
    <h4>Quick Links</h4>
    <ul class="footer-links">
      <li>Home</li><li>For Physicians</li>
      <li>About Us</li><li>PACS &amp; Documents</li>
      <li>Our Services</li><li>Appointments</li>
      <li>For Patients</li><li>Our Locations</li>
      <li>Our Physicians</li>
    </ul>
  </div>
  <div class="abs" style="left:477px;top:2390px;width:1px;height:150px;background:#555"></div>
  <div class="footer-col abs" style="left:522px;top:2392px">
    <h4>Quick Inquiry</h4>
    <div class="field">Name</div>
    <div class="field">Email</div>
    <div class="field message">Message</div>
    <span class="submit">Submit</span>
  </div>
  <div class="abs" style="left:763px;top:2390px;width:1px;height:150px;background:#555"></div>
  <div class="footer-col abs" style="left:810px;top:2392px;width:230px">
    <h4>Contact Details</h4>
    <div class="contact-row"><svg width="10" height="14" viewBox="0 0 10 14"><path d="M5 0a5 5 0 0 1 5 5c0 4-5 9-5 9S0 9 0 5a5 5 0 0 1 5-5z" fill="#ddd"/><circle cx="5" cy="5" r="2" fill="#333"/></svg><span>2285 NE Ridgeview Lane<br>Bend, Oregon 97700</span></div>
    <div class="contact-row"><svg width="12" height="12" viewBox="0 0 12 12"><path d="M2 1l2.5 2.5-1.2 1.3c.8 1.6 2 2.8 3.6 3.6l1.3-1.2L11 9.7 9.4 11.3C5.4 10.6 1.4 6.6.7 2.6z" fill="#ddd"/></svg><span>(541) 555-0148</span></div>
    <div class="contact-row" style="margin-top:26px"><svg width="13" height="10" viewBox="0 0 13 10"><rect width="13" height="10" fill="#ddd"/><path d="M0 0l6.5 5L13 0" fill="none" stroke="#333"/></svg><span>hello@phipclinic-example.com</span></div>
  </div>
  <div class="copyright abs">Copyright © 2016 - Pine Hollow Imaging Partners &nbsp;|&nbsp; All Right Reserved.</div>
  <div class="social abs"><span></span><span></span><span></span></div>
</footer>

</body>
</html>
```